Harrow Grading LLC business card design

Excavation company business cards

Contact Information for Business Card

Harrow Grading LLC cell phone 208-417-6290 office phone 208-319-4856 harrowgradingllc@maplecove.com Driveways, site prep, retaining walls, septic systems, rock delivery

Colors

Designer to choose colors to be used in the design.

```html
<!DOCTYPE html>
<html lang="en">
<head>
<meta charset="utf-8">
<title>Harrow Grading LLC – Business Card</title>
<link href="https://fonts.googleapis.com/css2?family=Arimo:wght@400;700&display=swap" rel="stylesheet">
<style>
  :root {
    --orange: #e96d1f;
    --white: #ffffff;
    --ink: #58595b;
    --backdrop: #d9d9d9;
  }
  * { margin: 0; padding: 0; box-sizing: border-box; }
  html, body {
    width: 1200px; height: 900px; overflow: hidden;
    background: var(--backdrop);
    font-family: "Arimo", Arial, sans-serif;
  }
  .canvas {
    width: 1200px; height: 900px;
    display: flex; flex-direction: column; align-items: center; justify-content: center;
    gap: 40px;
  }
  .card {
    width: 630px; height: 360px;
    border-radius: 26px;
    position: relative; overflow: hidden;
    box-shadow: 0 6px 18px rgba(0,0,0,0.18);
  }

  /* Front */
  .card--front {
    background: var(--orange); color: var(--white);
    display: flex; flex-direction: column; align-items: center; justify-content: center;
  }
  .brand {
    display: flex; align-items: center; gap: 14px;
    font-weight: 700; font-size: 40px; letter-spacing: 1px;
  }
  .brand__mark { width: 22px; height: 22px; background: currentColor; }
  .services {
    margin-top: 26px; text-align: center;
    font-size: 19px; line-height: 1.35;
  }
  .services .dot { margin: 0 6px; }

  /* Back */
  .card--back { background: var(--white); color: var(--ink); }
  .card--back .brand { position: absolute; left: 44px; top: 58px; color: var(--orange); font-size: 34px; }
  .person { position: absolute; left: 44px; top: 150px; }
  .person__name { color: var(--orange); font-size: 28px; font-weight: 400; letter-spacing: 1px; text-transform: uppercase; }
  .person__title { font-size: 20px; margin-top: 4px; }
  .contact { position: absolute; left: 44px; top: 232px; list-style: none; font-size: 20px; }
  .contact li { display: flex; align-items: center; gap: 12px; line-height: 31px; }
  .contact svg { width: 18px; height: 18px; flex: none; }
  .address {
    position: absolute; right: 40px; top: 150px;
    text-align: right; font-size: 18px; line-height: 1.35; font-style: normal;
  }
</style>
</head>
<body>
<main class="canvas">
  <section class="card card--front" aria-label="Card front">
    <div class="brand"><span class="brand__mark"></span>Harrow Grading LLC</div>
    <p class="services">
      Driveways<span class="dot">•</span>Site prep<span class="dot">•</span>Retaining walls<br>
      Septic systems<span class="dot">•</span>Rock delivery
    </p>
  </section>

  <section class="card card--back" aria-label="Card back">
    <div class="brand"><span class="brand__mark"></span>Harrow Grading LLC</div>
    <div class="person">
      <h1 class="person__name">Marcus Reed</h1>
      <p class="person__title">Managing Director</p>
    </div>
    <ul class="contact">
      <li>
        <svg viewBox="0 0 18 18" fill="none" stroke="var(--orange)" stroke-width="1.8"><rect x="4" y="1.5" width="10" height="15" rx="2"/><line x1="8" y1="13.5" x2="10" y2="13.5"/></svg>
        208-417-6290
      </li>
      <li>
        <svg viewBox="0 0 18 18" fill="var(--orange)"><path d="M4 1.5l3 3-1.8 2.2a10 10 0 0 0 6 6L13.5 11l3 3-2 2.5C8 16.5 1.5 10 1.5 3.5z"/></svg>
        208-319-4856
      </li>
      <li>
        <svg viewBox="0 0 18 18" fill="var(--orange)"><path d="M1 4h16v10H1z"/><path d="M1 4l8 6 8-6" fill="none" stroke="var(--white)" stroke-width="1.4"/></svg>
        harrowgradingllc@maplecove.com
      </li>
    </ul>
    <address class="address">
      421, Address line<br>
      goes here, 45452<br>
      Country Name
    </address>
  </section>
</main>
</body>
</html>
```